design a construction company business card

Design business card around our logo. Card must have all the typical info: name, title, address, phone, email, business name, etc. Somewhere on the card I would like to see our motto "Built on integrity... Inspired by commitment." Consider adding a splash of bright orange to the card to complement the blues and silvers/grays in the logo. We are open to metallic inks, textures, etc. We would like to see options on both light and dark backgrounds. The font in the logo is Euro Technic Extended Regular.

```html
<!DOCTYPE html>
<html lang="en">
<head>
<meta charset="utf-8">
<title>Hollis Contracting – Business Card</title>
<link href="https://fonts.googleapis.com/css2?family=Source+Sans+3:wght@400;600;700&display=swap" rel="stylesheet">
<style>
  :root {
    --page-bg: #e7e4df;
    --card-top: #f4f6f8;
    --card-bottom: #e6e9ed;
    --card-edge: #d2d6dc;
    --navy: #1b2470;
    --brand-blue: #2a3c8f;
    --ink: #1c1f2a;
    --ink-soft: #3a3d48;
    --divider: #6b6157;
    --motto: #e0907f;
  }
  * { margin: 0; padding: 0; box-sizing: border-box; }
  html, body {
    width: 1200px;
    height: 1120px;
    overflow: hidden;
    background: var(--page-bg);
    font-family: "Source Sans 3", Arial, sans-serif;
  }
  .business-card {
    position: absolute;
    left: 75px;
    top: 261px;
    width: 1050px;
    height: 598px;
    background: linear-gradient(160deg, var(--card-top), var(--card-bottom));
    border: 1px solid var(--card-edge);
    box-shadow: 0 10px 30px rgba(0,0,0,0.12);
  }
  .brand {
    position: absolute;
    left: 0;
    top: 0;
    width: 571px;
    height: 505px;
    display: flex;
    align-items: center;
    justify-content: center;
    gap: 16px;
  }
  .brand-square {
    width: 26px;
    height: 26px;
    background: var(--brand-blue);
  }
  .brand-name {
    font-size: 46px;
    font-weight: 700;
    color: var(--brand-blue);
    letter-spacing: 1px;
  }
  .divider {
    position: absolute;
    left: 571px;
    top: 150px;
    width: 2px;
    height: 292px;
    background: var(--divider);
    opacity: 0.7;
  }
  .contact {
    position: absolute;
    left: 630px;
    top: 160px;
    color: var(--ink);
  }
  .person-name {
    font-size: 36px;
    font-weight: 700;
    color: var(--navy);
    line-height: 1;
    letter-spacing: 0.5px;
  }
  .person-title {
    font-size: 27px;
    font-weight: 400;
    color: var(--ink-soft);
    line-height: 1;
    margin-top: 8px;
  }
  .address {
    font-size: 26px;
    line-height: 33px;
    margin-top: 26px;
  }
  .channels {
    list-style: none;
    margin-top: 20px;
  }
  .channels li {
    display: flex;
    align-items: center;
    gap: 18px;
    font-size: 26px;
    line-height: 34px;
  }
  .channels svg {
    width: 26px;
    height: 26px;
    fill: var(--navy);
    flex: none;
  }
  .motto-band {
    position: absolute;
    left: 0;
    top: 505px;
    width: 100%;
    height: 63px;
    background: linear-gradient(90deg, #2a3180 0%, var(--navy) 60%, #151c5e 100%);
  }
  .motto {
    position: absolute;
    left: 207px;
    top: 14px;
    font-size: 27px;
    color: var(--motto);
    white-space: nowrap;
  }
</style>
</head>
<body>
  <div class="business-card">
    <div class="brand">
      <span class="brand-square"></span>
      <span class="brand-name">Hollis Contracting, Inc.</span>
    </div>

    <div class="divider"></div>

    <div class="contact">
      <p class="person-name">MARK DELANEY</p>
      <p class="person-title">PRESIDENT</p>
      <p class="address">2417 Ridgecrest Avenue<br>Oak Hollow, NY 11230</p>
      <ul class="channels">
        <li>
          <svg viewBox="0 0 24 24" aria-hidden="true"><path d="M3 8c0-2 4-4 9-4s9 2 9 4v2h-4V8.5c-1-.6-3-1-5-1s-4 .4-5 1V10H3zM6 12l2-3h8l2 3v7H6zm6 1.5a2.5 2.5 0 1 0 0 5 2.5 2.5 0 0 0 0-5z"/></svg>
          555 0182 4419
        </li>
        <li>
          <svg viewBox="0 0 24 24" aria-hidden="true"><path d="M2 6h20v1l-10 6L2 7zm0 3l10 6 10-6v9H2z"/></svg>
          mark@hollisbuild.com
        </li>
        <li>
          <svg viewBox="0 0 24 24" aria-hidden="true"><path d="M12 2a10 10 0 1 0 0 20 10 10 0 0 0 0-20zm-1 3c-1 1-3 1-3 3s2 2 2 4-2 2-1 4l1 3a8 8 0 0 1-6-9c2 0 4-2 7-5zm4 1c1 2-1 3 0 5s3 1 3 4-2 4-3 4c0-2 1-3-1-4s-3-2-2-4 2-3 3-5z"/></svg>
          www.hollisbuild.com
        </li>
      </ul>
    </div>

    <div class="motto-band">
      <p class="motto">Built on integrity... Inspired by commitment.</p>
    </div>
  </div>
</body>
</html>
```